Online Shop Maren

We need a web design for an online shop, called "Lirvo Dune Jewels". The shop should have an extraordinary, elegant look, as shown in the Quellwick Advertising Picture in our Briefing.pdf (attached). Please have a look at our Briefing regarding website colours, background ideas, and elements to be included. The online shop is about professional jewellery design pieces, where each piece is handmade of high quality materials, also unique pieces and unique editions possible. It should attract extraordinary people and visualize that its a very individual and unique design jewellery. You can get an idea of whom it should attract by reading our target group. Colours to be used are jewellery-Velvet red, Black / anthracite, exclusive colours, silverish-white, bronze-brown and golden.

Please play around when designing with the image pictures we attach, preferably more vertical pictures, no panoramic pictures like in Brovenka Shop. Also include the BLACK logo of lirvo dune. We include the SITEMAP in the briefing and also another folder with product pictures you can use for the draft.

Regarding Functions, the store will have the SAME (technical) functions as this page:http://www.brovenka-shop.eu/ - using the "most famous" products/categories for the starting page, going into individual product pages by clicking these images and then leading to a detailed page for one product only.

Target Market(s)

Jewellery-lovers, who appreciate extraordinary things, creative economy/fashion-industries, stylists, Style consultants, outfitter, theatres, operas, production sites, Cocktail-, Dinner and Bridefashion, exclusive traditional costume stores, dancesports and tango argento dancers

Industry/Entity Type

Shop

Requirements
Must have
• Must include:
• Colours as per briefing
• Background ideas/images as per briefing/pictures sent
• Sitemap as per briefing
• Social buttons
• Logo
• Design for 3 pages: Starting page showing big images, attractive design and the 4 popular categories
• Subpage with different products of one category (i.e. bracelets)
• Detail page with one individual product only
Should not have
• no fresh, playful colours like yellow, orange, green, blue
• no cheap design, no panorama pictures

```html
<!DOCTYPE html>
<html lang="en">
<head>
<meta charset="utf-8">
<title>Lirvo Dune Jewels – Online Shop</title>
<link href="https://fonts.googleapis.com/css2?family=Merriweather:wght@400;700&family=Open+Sans:ital,wght@0,300;0,400;0,600;0,700;1,400&display=swap" rel="stylesheet">
<style>
:root{
  --red:#c1272d;
  --red-dark:#a31f24;
  --ink:#2b2b2b;
  --anthracite:#333333;
  --footer:#1c1c1c;
  --footer-deep:#2a2a2a;
  --paper:#ffffff;
  --card:#efefef;
}
*{box-sizing:border-box;margin:0;padding:0}
html,body{width:690px;height:1200px;overflow:hidden;background:var(--paper)}
body{font-family:"Open Sans",Arial,sans-serif;color:var(--ink);position:relative}
.page{position:relative;width:690px;height:1200px;overflow:hidden;background:linear-gradient(#fff,#fbfbfb)}
.abs{position:absolute}
.serif{font-family:"Merriweather",Georgia,serif}

/* top bar */
.topbar{left:0;top:0;width:690px;height:29px;background:var(--anthracite);color:#fff;font-size:6.5px}
.topbar .account{position:absolute;left:58px;top:10px}
.topbar .lang{position:absolute;right:62px;top:8px;display:flex;align-items:center;gap:4px}
.topbar .lang-select{width:40px;height:11px;background:#fff;color:#999;font-size:5px;padding:2px 3px;position:relative}
.topbar .lang-select::after{content:"";position:absolute;right:0;top:0;width:9px;height:11px;background:#6f86a8}

/* header */
.greeting{left:64px;top:55px;font-size:6px;font-style:italic}
.search{left:58px;top:76px;width:148px;height:18px;border:1px solid #ddd;background:#fff;font-size:6px;color:#aaa;padding:5px 7px}
.search svg{position:absolute;right:6px;top:4px}
.brand{left:0;width:690px;top:50px;text-align:center}
.brand .name{font-size:19px;font-weight:400;letter-spacing:.3px;color:#222}
.brand .sub{font-size:9px;margin-top:1px}
.support{right:62px;top:53px;font-size:6px;font-style:italic;display:flex;align-items:center;gap:5px}
.cartline{right:62px;top:79px;font-size:6px}

/* nav */
.nav{left:55px;top:114px;width:572px;height:30px;background:var(--anthracite);display:flex;justify-content:space-around;align-items:center;color:#fff;font-size:8px}

/* hero */
.hero-main{left:58px;top:168px;width:379px;height:184px;background:linear-gradient(90deg,#3a3430 0%,#5a4e48 45%,#9a8f8c 60%,#b9b0ae 100%)}
.hero-main .tagline{position:absolute;left:6px;top:73px;color:#fff;font-size:10px;line-height:17px}
.hero-side{left:448px;top:168px;width:179px;height:184px;background:radial-gradient(circle at 50% 40%,#d9d9d9 0%,#8a8a8a 40%,#2e2e2e 80%)}
.hero-side .offer{position:absolute;left:0;bottom:0;width:100%;height:39px;background:var(--red);color:#fff;font-size:9.5px;line-height:17px;padding:3px 8px;display:flex;justify-content:space-between}
.hero-side .offer s{color:#f3d6d6}

/* welcome */
.welcome{left:0;top:382px;width:690px;text-align:center;font-size:14px;font-weight:400}
.welcome em{font-style:normal;color:var(--red)}
.intro{left:70px;top:409px;width:550px;text-align:center;font-size:6.3px;line-height:11px}

/* section headings */
.section-title{font-family:"Merriweather",Georgia,serif;font-size:13px;font-weight:400;border-bottom:1px solid var(--ink);padding-bottom:4px}
.recent-title{left:55px;top:454px;width:407px}

/* products */
.product{width:94px;height:151px;background:var(--card);text-align:center}
.product .photo{height:71px;background:radial-gradient(circle at 50% 55%,#6b6b6b 0%,#262626 55%,#111 100%)}
.product .photo.gold{background:radial-gradient(circle at 50% 55%,#d8cdb8 0%,#7c7262 45%,#1f1f1f 90%)}
.product .photo.silver{background:radial-gradient(circle at 50% 55%,#cfcfcf 0%,#777 45%,#1c1c1c 90%)}
.product .title{font-family:"Merriweather",Georgia,serif;font-size:6.2px;line-height:10px;margin-top:6px}
.product .price{color:var(--red);font-size:7px;margin-top:1px}
.product-actions{font-size:5.5px;color:#666;line-height:10px;margin-top:3px;text-align:left;padding-left:18px}
.product .add{display:inline-block;background:var(--red);color:#fff;font-size:5px;padding:2px 4px;margin-top:3px;border:1px solid var(--red-dark)}

/* promos */
.promo-wide{left:55px;top:815px;width:264px;height:117px;background:linear-gradient(90deg,#1b1b1b,#3a3833 40%,#6b5d3a 70%,#222);color:#fff}
.promo-wide .text{position:absolute;left:14px;top:7px;right:20px;display:flex;justify-content:space-between;font-size:10px}
.promo-small{left:326px;top:815px;width:134px;height:117px;background:radial-gradient(circle at 50% 55%,#e0d6c2 0%,#8a7d62 40%,#2a2a2a 85%);color:#fff}
.promo-small .text{position:absolute;left:54px;top:20px;font-size:10px;line-height:16px}

/* sidebar */
.side-title{left:491px;top:458px;width:136px;font-size:10.5px}
.categories{left:491px;top:480px;list-style:none}
.categories li{font-family:"Merriweather",Georgia,serif;color:var(--red);font-size:10px;line-height:17.5px;display:flex;align-items:center;gap:6px}
.categories li svg{flex:none}

.cart{left:486px;top:618px;width:141px;height:175px;background:#fff;border:3px solid #3b3b3b}
.cart .head{height:19px;background:#3b3b3b;color:#fff;font-size:5.5px;font-weight:700;display:flex;align-items:center}
.cart .head .label{display:flex;align-items:center;gap:4px;padding-left:6px;flex:1;height:100%}
.cart .head .count{background:#555;color:#ddd;font-weight:400;height:100%;padding:0 6px;display:flex;align-items:center;gap:6px}
.cart .item{position:absolute;left:3px;width:129px;height:34px}
.cart .thumb{position:absolute;left:0;top:2px;width:34px;height:30px;background:radial-gradient(circle,#bbb,#222 80%)}
.cart .thumb.gold{background:radial-gradient(circle,#d6c18e,#222 80%)}
.cart .thumb.dark{background:radial-gradient(circle,#555,#111 80%)}
.cart .iname{position:absolute;left:40px;top:0;font-family:"Merriweather",Georgia,serif;font-size:5px;text-decoration:underline}
.cart .row{position:absolute;left:40px;top:16px;width:88px;height:10px;background:#e9e9e9;font-size:7px;display:flex;align-items:center;padding-left:2px}
.cart .row .x{color:var(--red);font-size:5px;margin-left:auto;margin-right:3px}
.cart .row .qty{width:22px;height:8px;background:#fff;border:1px solid #bbb;font-size:5px;text-align:right;padding-right:2px;margin-right:8px}
.cart .row .remove{position:absolute;right:-2px;top:1px}
.cart .total{position:absolute;left:0;bottom:0;width:100%;height:24px;background:#3b3b3b;color:#fff;display:flex;align-items:center;padding:0 6px;font-size:5.5px;font-weight:700}
.cart .total .sum{font-size:12px;font-weight:400;margin-left:6px}
.cart .total .checkout{margin-left:auto;background:var(--red);border-radius:7px;font-size:5px;padding:2px 6px}

.social-title{left:483px;top:811px;width:143px;font-size:10.5px}
.social{left:483px;top:835px;width:143px;height:96px;background:#f3f3f3;border:1px solid #e2e2e2}
.social .avatar{position:absolute;left:12px;top:6px;width:30px;height:28px;background:radial-gradient(circle,#cab98e,#3a3a3a 85%)}
.social .page-name{position:absolute;left:46px;top:8px;font-size:6px;color:#4a5c8a}
.social .like{position:absolute;left:46px;top:20px;border:1px solid #c9c9c9;background:#fff;font-size:5.5px;padding:1px 5px;color:#555}
.social .fans{position:absolute;left:12px;top:44px;font-size:5.3px;color:#555}
.social .fans b{font-weight:400;color:#4a5c8a}
.social .faces{position:absolute;left:12px;top:59px;display:flex;gap:2px}
.social .faces span{width:29px;height:30px;background:linear-gradient(#8a7a6a,#3e352e)}

/* footer */
.footer{left:0;top:965px;width:690px;height:190px;background:var(--footer);color:#cfcfcf}
.footer h3{position:absolute;top:19px;font-weight:400;font-size:12px;color:#eaeaea;letter-spacing:.3px}
.touch{position:absolute;left:65px;top:44px;font-size:6.5px;list-style:none}
.touch li{display:flex;align-items:flex-start;gap:7px;height:20px}
.cards{position:absolute;left:66px;top:164px;display:flex;gap:3px}
.cards span{width:16px;height:10px;background:#d9d9d9;border-radius:1px}
.useful-links{position:absolute;left:224px;top:44px;width:98px;list-style:none;font-size:5.8px}
.useful-links li{height:17.5px;border-bottom:1px solid #2f2f2f;display:flex;align-items:center;gap:5px;padding-left:7px;color:#e5e5e5}
.useful-links li.active{background:var(--red);color:#fff}
.news{position:absolute;left:361px;top:44px;list-style:none}
.news li{position:relative;height:44px}
.news .pic{position:absolute;left:0;top:0;width:35px;height:33px;background:linear-gradient(#cfd3d6,#6e6e6e);border:2px solid #fff}
.news .t{position:absolute;left:44px;top:10px;font-size:5.8px;white-space:nowrap;color:#e5e5e5}
.news .d{position:absolute;left:44px;top:20px;font-size:4.8px;color:#999;white-space:nowrap}
.contact-form{position:absolute;left:503px;top:43px;width:122px}
.field{background:#2d2d2d;height:18px;margin-bottom:5px;font-size:5.5px;color:#9a9a9a;padding:5px 6px}
.field.msg{height:64px}
.submit{display:inline-block;background:#fff;color:#222;font-size:6px;font-weight:600;padding:4px 12px;border:1px solid #999}

.bottombar{left:0;top:1155px;width:690px;height:45px;background:var(--footer-deep);color:#fff}
.bottombar .logo{position:absolute;left:62px;top:8px;font-size:12.5px;font-weight:400}
.bottombar .logo small{display:block;font-size:6px;margin-left:20px;margin-top:1px}
.bottombar .pay{position:absolute;right:62px;top:15px;display:flex;align-items:center;gap:3px}
.bottombar .pay span{width:18px;height:12px;background:#e4e4e4;border-radius:1px}
.bottombar .pay b{font-size:12px;font-weight:700;margin-left:10px}
</style>
</head>
<body>
<div class="page">

  <div class="abs topbar">
    <div class="account">My Account | Wishlist | Check out | Login</div>
    <div class="lang">Your Language : <div class="lang-select">English</div></div>
  </div>

  <header>
    <div class="abs greeting">Welcome to our online store!</div>
    <div class="abs search">Search entire store here...
      <svg width="9" height="9" viewBox="0 0 10 10"><circle cx="4" cy="4" r="3" fill="none" stroke="#999" stroke-width="1.2"/><line x1="6.3" y1="6.3" x2="9.3" y2="9.3" stroke="#999" stroke-width="1.4"/></svg>
    </div>
    <div class="abs brand">
      <div class="name">Lirvo Dune</div>
      <div class="sub">♦ Jewels ♦</div>
    </div>
    <div class="abs support">
      <svg width="12" height="11" viewBox="0 0 12 11"><path d="M2 3 Q6 -1 10 3 L8.5 4.5 Q6 2.5 3.5 4.5 Z" fill="#555"/><rect x="4" y="5" width="4" height="5" rx="1" fill="#555"/></svg>
      Support +120 555 014 2210
    </div>
    <div class="abs cartline">Shopping Cart - CartSubtotal:$0.00</div>
  </header>

  <nav class="abs nav">
    <span>Home</span><span>Online Shop</span><span>Info &amp; Facts</span><span>Partner</span><span>About me</span><span>Contact</span>
  </nav>

  <section class="abs hero-main" role="img" aria-label="Model in a lace dress standing by a window with her shadow on the wall">
    <div class="tagline serif">Ever Best Collection Of Jwellery<br>Presents By<br>Lirvo Dune Jewels</div>
  </section>
  <section class="abs hero-side" role="img" aria-label="Crystal beaded bracelets on black velvet">
    <div class="offer serif"><span>Just Take 50% off<br>And Get Bracelet :</span><span><s>$664.654</s><br>$325.654</span></div>
  </section>

  <h1 class="abs welcome serif">Welcome To <em>Lirvo Dune Jewels</em></h1>
  <p class="abs intro">Lorem Ipsum est simplement du faux texte employé dans la sition et la misen page avant impression. Le Lorem Ipsum est le faux texte standard de l'imprimerie depuis les années 1500, quand un peintre anonyme assembla ensemble des morceaux de texte pour réaliser un livre spécimen de polices de texte.</p>

  <h2 class="abs section-title recent-title">Recent Products</h2>

  <div class="abs product" style="left:55px;top:482px">
    <div class="photo" role="img" aria-label="Black diamond necklace"></div>
    <div class="title">Black Diamond<br>Neckless</div><div class="price">$ 200.44</div>
    <div class="product-actions">+ Add to Wishlist<br>+ Add to Compare</div><span class="add">Add to Cart</span>
  </div>
  <div class="abs product" style="left:160px;top:482px">
    <div class="photo silver" role="img" aria-label="Silver stone earring"></div>
    <div class="title">Silver Stone<br>Earring</div><div class="price">$ 150.44</div>
    <div class="product-actions">+ Add to Wishlist<br>+ Add to Compare</div><span class="add">Add to Cart</span>
  </div>
  <div class="abs product" style="left:264px;top:482px">
    <div class="photo" role="img" aria-label="Black cored necklace"></div>
    <div class="title">Black Cored<br>Neckless</div><div class="price">$ 540.64</div>
    <div class="product-actions">+ Add to Wishlist<br>+ Add to Compare</div><span class="add">Add to Cart</span>
  </div>
  <div class="abs product" style="left:368px;top:482px">
    <div class="photo gold" role="img" aria-label="Golden diamond necklace"></div>
    <div class="title">Golden Diamond<br>Neckless</div><div class="price">$ 476.44</div>
    <div class="product-actions">+ Add to Wishlist<br>+ Add to Compare</div><span class="add">Add to Cart</span>
  </div>

  <div class="abs product" style="left:55px;top:649px">
    <div class="photo silver" role="img" aria-label="Golden diamond earring"></div>
    <div class="title">Golden Diamond<br>Earring</div><div class="price">$ 340.44</div>
    <div class="product-actions">+ Add to Wishlist<br>+ Add to Compare</div><span class="add">Add to Cart</span>
  </div>
  <div class="abs product" style="left:160px;top:649px">
    <div class="photo gold" role="img" aria-label="Golden diamond ring"></div>
    <div class="title">Golden Diamond<br>Ring</div><div class="price">$ 466.44</div>
    <div class="product-actions">+ Add to Wishlist<br>+ Add to Compare</div><span class="add">Add to Cart</span>
  </div>
  <div class="abs product" style="left:264px;top:649px">
    <div class="photo" role="img" aria-label="Black bangle"></div>
    <div class="title">Black Dieyn<br>Bengle</div><div class="price">$ 756.64</div>
    <div class="product-actions">+ Add to Wishlist<br>+ Add to Compare</div><span class="add">Add to Cart</span>
  </div>
  <div class="abs product" style="left:368px;top:649px">
    <div class="photo gold" role="img" aria-label="Bronze diamond necklace"></div>
    <div class="title">Bron Diamond<br>Neckless</div><div class="price">$ 223.34</div>
    <div class="product-actions">+ Add to Wishlist<br>+ Add to Compare</div><span class="add">Add to Cart</span>
  </div>

  <section class="abs promo-wide" role="img" aria-label="Silver and gold crystal bangles">
    <div class="text serif"><span>Get Modern Design In Just</span><span>$215.86</span></div>
  </section>
  <section class="abs promo-small" role="img" aria-label="Crystal net necklace">
    <div class="text serif">Just In<br>$43.34</div>
  </section>

  <aside>
    <h2 class="abs section-title side-title">Products</h2>
    <ul class="abs categories">
      <li><svg width="7" height="5" viewBox="0 0 7 5"><path d="M0 2.5H6M4 0.5L6 2.5L4 4.5" stroke="#222" fill="none"/></svg>Collier</li>
      <li><svg width="7" height="5" viewBox="0 0 7 5"><path d="M0 2.5H6M4 0.5L6 2.5L4 4.5" stroke="#222" fill="none"/></svg>Bracelet</li>
      <li><svg width="7" height="5" viewBox="0 0 7 5"><path d="M0 2.5H6M4 0.5L6 2.5L4 4.5" stroke="#222" fill="none"/></svg>Ring</li>
      <li><svg width="7" height="5" viewBox="0 0 7 5"><path d="M0 2.5H6M4 0.5L6 2.5L4 4.5" stroke="#222" fill="none"/></svg>Earring</li>
      <li><svg width="7" height="5" viewBox="0 0 7 5"><path d="M0 2.5H6M4 0.5L6 2.5L4 4.5" stroke="#222" fill="none"/></svg>Bengle</li>
      <li><svg width="7" height="5" viewBox="0 0 7 5"><path d="M0 2.5H6M4 0.5L6 2.5L4 4.5" stroke="#222" fill="none"/></svg>Neckless</li>
      <li><svg width="7" height="5" viewBox="0 0 7 5"><path d="M0 2.5H6M4 0.5L6 2.5L4 4.5" stroke="#222" fill="none"/></svg>Earring</li>
    </ul>

    <div class="abs cart">
      <div class="head">
        <div class="label"><svg width="10" height="8" viewBox="0 0 10 8"><path d="M0 0.5H2L3 5H8.5L9.5 1.5H2.5" stroke="#ccc" fill="none"/><circle cx="3.5" cy="7" r=".8" fill="#ccc"/><circle cx="8" cy="7" r=".8" fill="#ccc"/></svg>SHOPPING CART</div>
        <div class="count">3 items <span>|</span> $231</div>
      </div>
      <div class="item" style="top:23px"><div class="thumb" role="img" aria-label="Bracelet"></div><div class="iname">Bracelets</div>
        <div class="row">$30<span class="x">x</span><span class="qty">1</span><svg class="remove" width="8" height="8" viewBox="0 0 8 8"><circle cx="4" cy="4" r="4" fill="#d0151b"/><rect x="2" y="3.4" width="4" height="1.2" fill="#fff"/></svg></div></div>
      <div class="item" style="top:62px"><div class="thumb gold" role="img" aria-label="Diamond necklace"></div><div class="iname">Diamond Necklesses</div>
        <div class="row">$101<span class="x">x</span><span class="qty">1</span><svg class="remove" width="8" height="8" viewBox="0 0 8 8"><circle cx="4" cy="4" r="4" fill="#d0151b"/><rect x="2" y="3.4" width="4" height="1.2" fill="#fff"/></svg></div></div>
      <div class="item" style="top:101px"><div class="thumb dark" role="img" aria-label="Collier"></div><div class="iname">Collier</div>
        <div class="row">$100<span class="x">x</span><span class="qty">1</span><svg class="remove" width="8" height="8" viewBox="0 0 8 8"><circle cx="4" cy="4" r="4" fill="#d0151b"/><rect x="2" y="3.4" width="4" height="1.2" fill="#fff"/></svg></div></div>
      <div class="total">Total: <span class="sum">$231</span><span class="checkout">CHECK OUT »</span></div>
    </div>

    <h2 class="abs section-title social-title">Circlepage</h2>
    <div class="abs social">
      <div class="avatar" role="img" aria-label="Page thumbnail of a necklace"></div>
      <div class="page-name">Lirvo Dune Jewellery</div>
      <div class="like">Like</div>
      <div class="fans">39 people like <b>Lirvo Dune Jewellery.</b></div>
      <div class="faces" role="img" aria-label="Follower photos"><span></span><span></span><span></span><span></span></div>
    </div>
  </aside>

  <footer class="abs footer">
    <h3 style="left:65px">Get in Touch</h3>
    <ul class="touch">
      <li><svg width="8" height="8" viewBox="0 0 8 8"><path d="M1 0.5L2.8 0.5L3.3 2.5L2.2 3.3Q3 5 4.7 5.8L5.5 4.7L7.5 5.2L7.5 7Q3.5 7.5 0.5 2.5Z" fill="#bbb"/></svg>(+1) 555 014 7890</li>
      <li><svg width="8" height="8" viewBox="0 0 8 8"><circle cx="4" cy="4" r="3.3" fill="none" stroke="#bbb"/><path d="M4 2V4H5.5" stroke="#bbb" fill="none"/></svg>Mon - Fri&nbsp; 10:00am - 5:30 pm</li>
      <li><svg width="8" height="8" viewBox="0 0 8 8"><rect x="0.5" y="1.5" width="7" height="5" fill="#bbb"/><path d="M0.5 1.5L4 4.5L7.5 1.5" stroke="#1c1c1c" fill="none"/></svg>Mon - Fri&nbsp; 10:00am - 5:30 pm</li>
      <li><svg width="8" height="8" viewBox="0 0 8 8"><circle cx="4" cy="4" r="3.3" fill="none" stroke="#bbb"/><ellipse cx="4" cy="4" rx="1.4" ry="3.3" fill="none" stroke="#bbb"/><line x1="0.7" y1="4" x2="7.3" y2="4" stroke="#bbb"/></svg>Mon - Fri&nbsp; 10:00am - 5:30 pm</li>
      <li><svg width="8" height="9" viewBox="0 0 8 9"><path d="M4 8.5Q0.5 4.5 0.5 3A3.5 3.5 0 0 1 7.5 3Q7.5 4.5 4 8.5Z" fill="#bbb"/><circle cx="4" cy="3" r="1.2" fill="#1c1c1c"/></svg><span>Mon - Fri&nbsp; 10:00am - 5:30 pm<br>Harrow Lane TF - 480211</span></li>
    </ul>
    <div class="cards" aria-label="Accepted payment methods"><span></span><span></span><span></span><span></span><span></span></div>

    <h3 style="left:223px">Useful Links</h3>
    <ul class="useful-links">
      <li>→ Neck lace</li><li class="active">→ Ring</li><li>→ Wrist gold watch</li><li>→ Wrist Diamond watch</li><li>→ Breslate</li><li>→ Wrist gold watch</li><li>→ Wrist Diamond watch</li>
    </ul>

    <h3 style="left:360px">Latest News</h3>
    <ul class="news">
      <li><div class="pic" role="img" aria-label="News photo"></div><span class="t">Just a Single Clean Post</span><span class="d">february 03, 2013</span></li>
      <li><div class="pic" role="img" aria-label="News photo"></div><span class="t">Just a Single Clean Post</span><span class="d">february 10, 2013</span></li>
      <li><div class="pic" role="img" aria-label="News photo"></div><span class="t">Just a Single Clean Post</span><span class="d">february 15, 2013</span></li>
    </ul>

    <h3 style="left:506px">Contact Us</h3>
    <form class="contact-form">
      <div class="field">Name*</div>
      <div class="field">Email Address*</div>
      <div class="field msg">Message*</div>
      <span class="submit">SUBMIT</span>
    </form>
  </footer>

  <div class="abs bottombar">
    <div class="logo">Lirvo Dune<small>• Jewels •</small></div>
    <div class="pay"><span></span><span></span><span></span><b>Paynest</b></div>
  </div>

</div>
</body>
</html>
```